NEW Modern Sleek Business Card for VR Language Startup

Our startup is using VR to lead the next wave of world language education. We need a two-sided business card that introduces the larger organization (Brightloom Language Inc) and our contact info on one side and shows the product, Glimwoorld, on the other side.

Side 1 (contact info)= Brightloom Logo and Contact info (name, title, phone, email)

Side 2 (product)= Glimworld logo, text, and website
Text= Culturally Immersive Language Learning Games
Website= www.glimworld-play.com

Target Market(s)

Education, Technology

Contact Information for Business Card

Contact info will be updated upon approval of the design. For now, put this as a placeholder.

Perry Dunmore
Founder & CEO
pdunmore@quillpost-mail.net
(555)-014-2286

Font styles to use
Other font styles liked:
• Gibson and Century Gothic are the brand fonts

Requirements
Nice to have
• I would love to see cohesion between the design and colors of the two logos. I have attached a few business card designs that I like, so you can get a feel for my preferred style.

```html
<!DOCTYPE html>
<html lang="en">
<head>
<meta charset="utf-8">
<title>Brightloom Language Inc – Business Card</title>
<link href="https://fonts.googleapis.com/css2?family=Montserrat:wght@300;400;600;700&display=swap" rel="stylesheet">
<style>
  :root {
    --backdrop: #2a2b2e;
    --card-white: #ffffff;
    --card-black: #1c1c1e;
    --ink: #1a1a1a;
    --ink-soft: #3a3a3a;
    --tagline-grey: #5d5d62;
    --accent-blue: #4aa6e8;
    --text-white: #ffffff;
    --art-orange: #f2653a;
    --art-red: #e8365a;
    --art-purple: #8a4fc8;
    --art-violet: #5b5fd6;
    --art-cyan: #2ec4f0;
  }
  * { margin: 0; padding: 0; box-sizing: border-box; }
  html, body {
    width: 1200px;
    height: 900px;
    overflow: hidden;
    background: var(--backdrop);
    font-family: "Montserrat", sans-serif;
  }
  .canvas {
    position: relative;
    width: 1200px;
    height: 900px;
  }
  .card {
    position: absolute;
    left: 280px;
    width: 640px;
    height: 366px;
    border-radius: 28px;
    overflow: hidden;
    box-shadow: 0 14px 30px rgba(0,0,0,0.45);
  }
  /* Side 1: contact */
  .card--contact {
    top: 44px;
    background: var(--card-white);
    color: var(--ink);
  }
  .hero-art {
    position: absolute;
    left: 0;
    top: 96px;
    width: 250px;
    height: 270px;
    border-radius: 0 110px 40px 0;
    background: linear-gradient(165deg,
      var(--art-orange) 0%,
      var(--art-red) 28%,
      var(--art-purple) 55%,
      var(--art-violet) 72%,
      var(--art-cyan) 100%);
  }
  .brand {
    position: absolute;
    top: 44px;
    right: 46px;
    display: flex;
    align-items: center;
    gap: 12px;
  }
  .brand__name {
    font-weight: 600;
    font-size: 34px;
    letter-spacing: 0.14em;
    text-transform: uppercase;
    color: var(--ink);
  }
  .brand__dot {
    width: 16px;
    height: 16px;
    border-radius: 50%;
    background: var(--art-red);
  }
  .person {
    position: absolute;
    top: 150px;
    right: 46px;
    text-align: right;
  }
  .person__name {
    font-weight: 700;
    font-size: 24px;
    letter-spacing: 0.02em;
    text-transform: uppercase;
  }
  .person__title {
    font-weight: 400;
    font-size: 15px;
    letter-spacing: 0.04em;
    text-transform: uppercase;
    color: var(--ink-soft);
    margin-top: 2px;
  }
  .contact {
    position: absolute;
    top: 250px;
    right: 46px;
    text-align: right;
    font-weight: 400;
    font-size: 16px;
    line-height: 1.35;
    text-transform: uppercase;
    color: var(--ink-soft);
  }
  /* Side 2: product */
  .card--product {
    top: 494px;
    background: var(--card-black);
    color: var(--text-white);
    text-align: center;
  }
  .product-mark {
    position: absolute;
    top: 46px;
    left: 50%;
    transform: translateX(-50%);
    width: 96px;
    height: 96px;
    border-radius: 50%;
    background: linear-gradient(90deg, var(--art-cyan), var(--art-violet));
  }
  .product__name {
    position: absolute;
    top: 160px;
    left: 0;
    right: 0;
    font-weight: 600;
    font-size: 54px;
    letter-spacing: 0.01em;
    color: var(--text-white);
  }
  .product__tagline {
    position: absolute;
    top: 252px;
    left: 0;
    right: 0;
    font-weight: 400;
    font-size: 15px;
    letter-spacing: 0.06em;
    text-transform: uppercase;
    color: var(--tagline-grey);
  }
  .product__site {
    position: absolute;
    top: 282px;
    left: 0;
    right: 0;
    font-weight: 400;
    font-size: 17px;
    letter-spacing: 0.05em;
    text-transform: uppercase;
    color: var(--text-white);
  }
</style>
</head>
<body>
<main class="canvas">
  <section class="card card--contact" aria-label="Contact side">
    <div class="hero-art" role="img" aria-label="Large gradient artwork in orange, red, purple and cyan tones"></div>
    <div class="brand">
      <span class="brand__name">Brightloom</span>
      <span class="brand__dot"></span>
    </div>
    <div class="person">
      <p class="person__name">Perry Dunmore</p>
      <p class="person__title">Founder &amp; CEO</p>
    </div>
    <div class="contact">
      <p>pdunmore@quillpost-mail.net</p>
      <p>(555)-014-2286</p>
    </div>
  </section>

  <section class="card card--product" aria-label="Product side">
    <div class="product-mark"></div>
    <p class="product__name">Glimworld</p>
    <p class="product__tagline">Culturally Immersive Language Learning Games</p>
    <p class="product__site">www.glimworld-play.com</p>
  </section>
</main>
</body>
</html>
```